New Business Card for Web Design/Internet Marketing Company

Looking for a great looking new business card. We are a 10 year old web design, internet marketing and website management company that works mostly with small businesses.

Our new card needs to better match the colors and style of our website, be bold, extremely usable and slightly edgy.

Target Market(s)

Small/Medium businesses that have websites

Industry/Entity Type

Internet

Requirements
Must have
• Front and back design, full color, rounded corners please

Must use the colors/style of our website (JPG provided)

INFO FOR CARDS (as readable as possible please)
Mark Lenner
President/CEO
mark@trelvanmedia.example
Phone: 520-381-7459
Toll Free: 866-381-7459
Address: 4315 W. Calloway Ave. Ste. 140, Tucson, AZ 85792

THINGS I WANT TO PROMOTE (if there is room):
1. Our Website - www.trelvanmedia.example

2. Social Media
Twitter: @trelvanmedia
Facebook: www.facebook.com/trelvanmedia

3. Our Services
Web Design
Internet Marketing
Website Management

```html
<!DOCTYPE html>
<html lang="en">
<head>
<meta charset="utf-8">
<title>Trelvan Media – Business Card, Front and Back</title>
<link rel="stylesheet" href="https://fonts.googleapis.com/css2?family=Source+Sans+3:wght@400;600;700&display=swap">
<style>
  :root {
    --stage: #9a6644;
    --card-white: #ffffff;
    --card-grey: #5f5f61;
    --band-grey: #6b6b6d;
    --brand-blue: #1a8fcb;
    --brand-orange: #f07f23;
    --text-dark: #3d3d3d;
    --text-light: #ffffff;
    --rule: #c9c9c9;
  }
  * { box-sizing: border-box; margin: 0; padding: 0; }
  html, body {
    width: 1200px;
    height: 402px;
    overflow: hidden;
    background: var(--stage);
    font-family: "Source Sans 3", "Myriad Pro", Arial, sans-serif;
  }
  .card {
    position: absolute;
    top: 60px;
    width: 533px;
    height: 293px;
    border-radius: 10px;
    overflow: hidden;
    box-shadow: 0 2px 6px rgba(0, 0, 0, 0.25);
  }

  /* ---------- Front ---------- */
  .card--front { left: 61px; background: var(--card-white); }
  .card__waves { position: absolute; left: 0; top: 0; width: 533px; height: 293px; }

  .brand {
    position: absolute;
    left: 22px;
    top: 96px;
    width: 256px;
    display: flex;
    align-items: center;
    justify-content: center;
    gap: 8px;
  }
  .brand__dot {
    width: 22px; height: 22px; border-radius: 50%;
    background: var(--brand-blue);
    flex: none;
  }
  .brand__name {
    font-size: 34px;
    font-weight: 700;
    letter-spacing: -0.5px;
    color: var(--brand-orange);
    line-height: 1;
    white-space: nowrap;
  }

  .divider {
    position: absolute;
    left: 301px;
    top: 42px;
    width: 1px;
    height: 140px;
    background: var(--rule);
  }
  .person { position: absolute; left: 313px; top: 44px; }
  .person__name { font-size: 18px; font-weight: 600; color: var(--brand-blue); line-height: 1.1; }
  .person__title { font-size: 12px; color: var(--brand-blue); }

  .contact {
    position: absolute;
    left: 313px;
    top: 106px;
    list-style: none;
    font-size: 13px;
    color: var(--text-dark);
  }
  .contact li { display: flex; align-items: center; gap: 5px; height: 19px; white-space: nowrap; }
  .contact svg { width: 10px; height: 10px; flex: none; }

  .address {
    position: absolute;
    left: 287px;
    top: 244px;
    font-size: 13px;
    line-height: 20px;
    color: var(--text-light);
    white-space: nowrap;
  }

  /* ---------- Back ---------- */
  .card--back { left: 625px; background: var(--card-grey); color: var(--text-light); text-align: center; }
  .back__brand {
    position: absolute;
    left: 0; right: 0; top: 78px;
    font-size: 40px;
    font-weight: 700;
    letter-spacing: -0.5px;
    line-height: 1;
    color: var(--text-light);
  }
  .services { position: absolute; left: 0; right: 0; top: 158px; }
  .services__title {
    display: inline-block;
    font-size: 21px;
    font-weight: 600;
    padding: 0 8px 2px;
    border-bottom: 2px solid var(--text-light);
    width: 172px;
  }
  .services__list { margin-top: 14px; font-size: 19px; line-height: 26px; }
  .social {
    position: absolute;
    left: 0; right: 0; top: 267px;
    display: flex; justify-content: center; gap: 40px;
    font-size: 13px;
  }
</style>
</head>
<body>

<section class="card card--front" aria-label="Card front">
  <svg class="card__waves" viewBox="0 0 533 293" aria-hidden="true">
    <path d="M0 200 C120 250 240 225 360 205 C430 193 490 205 533 222 L533 293 L0 293 Z" fill="var(--band-grey)"/>
    <path d="M0 218 C130 250 250 212 360 192 C440 178 500 190 533 212 L533 218 C495 198 440 188 370 202 C260 225 140 258 0 232 Z" fill="var(--brand-orange)"/>
    <path d="M0 188 C80 220 180 232 280 218 C200 240 90 236 0 206 Z" fill="var(--brand-blue)"/>
  </svg>

  <div class="brand">
    <span class="brand__dot"></span>
    <span class="brand__name">Trelvan Media</span>
  </div>

  <div class="divider"></div>
  <div class="person">
    <p class="person__name">Mark Lenner</p>
    <p class="person__title">President/CEO</p>
  </div>

  <ul class="contact">
    <li><svg viewBox="0 0 10 10"><circle cx="5" cy="5" r="5" fill="#3d3d3d"/><path d="M3 2.5 L4.3 2.5 L4.8 4 L4 4.6 C4.5 5.5 5 6 5.8 6.4 L6.4 5.6 L7.8 6.1 L7.8 7.4 C5 7.6 2.8 5.2 3 2.5 Z" fill="#fff"/></svg>520-381-7459</li>
    <li><svg viewBox="0 0 10 10"><circle cx="5" cy="5" r="5" fill="#3d3d3d"/><path d="M3.5 2 L6.5 2 L6.5 8 L3.5 8 Z" fill="#fff"/></svg>866-381-7459</li>
    <li><svg viewBox="0 0 10 10"><rect x="0" y="2" width="10" height="7" fill="#3d3d3d"/><path d="M0.5 2.5 L5 6 L9.5 2.5" stroke="#fff" fill="none"/></svg>mark@trelvanmedia.example</li>
    <li><svg viewBox="0 0 10 10" fill="none" stroke="#3d3d3d"><circle cx="5" cy="5" r="4.5"/><ellipse cx="5" cy="5" rx="2" ry="4.5"/><path d="M0.5 5 H9.5"/></svg>www.trelvanmedia.example</li>
  </ul>

  <p class="address">4315 W. Calloway Ave. Ste. 140<br>Tucson, AZ 85792</p>
</section>

<section class="card card--back" aria-label="Card back">
  <p class="back__brand">Trelvan Media</p>
  <div class="services">
    <h2 class="services__title">Our Services</h2>
    <p class="services__list">Web Design &nbsp;•&nbsp; Internet Marketing<br>Website Management</p>
  </div>
  <div class="social">
    <span>@trelvanmedia</span>
    <span>trelvanmedia</span>
  </div>
</section>

</body>
</html>
```